BOLD & MINIMALIST DESIGN NEEDED

We want a very bold but minimalistic business card design that is impactful and utilizes both sides of the business card. Our current logo is included for your use.

We want bold fonts and good use of negative space. We don't want the logo to overpower the design.

Target Market(s)

Professionals who are building new commercial buildings.

Industry/Entity Type

Construction

Contact Information for Business Card

Name, Title, email, office phone, cell phone, website

Font styles to use
Serif
Sans Serif

Requirements
Must have
• Bold design!

```html
<!DOCTYPE html>
<html lang="en">
<head>
<meta charset="utf-8">
<title>Ridgecrest Business Card</title>
<link href="https://fonts.googleapis.com/css2?family=Roboto:wght@400;700;900&display=swap" rel="stylesheet">
<style>
  :root {
    --bg: #e4e4e4;
    --ink: #050505;
    --paper: #f4f4f4;
    --green: #7dbb25;
    --green-light: #a9d46a;
    --white: #ffffff;
  }
  * { margin: 0; padding: 0; box-sizing: border-box; }
  html, body {
    width: 1200px; height: 1040px; overflow: hidden;
    background: var(--bg);
    font-family: "Roboto", Arial, sans-serif;
  }
  .canvas { position: relative; width: 1200px; height: 1040px; }
  .card {
    position: absolute; width: 640px; height: 364px;
    border-radius: 16px; overflow: hidden;
  }
  .card--front { left: 285px; top: 130px; background: var(--ink); }
  .card--back {
    left: 284px; top: 568px; width: 646px; height: 368px;
    background: radial-gradient(ellipse at 48% 45%, var(--green-light) 0%, var(--green) 75%);
    display: flex; align-items: center; justify-content: center;
  }
  .front-shape { position: absolute; inset: 0; }
  .contact { position: absolute; left: 42px; top: 85px; color: var(--white); }
  .contact__name {
    color: var(--green); font-weight: 700; font-size: 24px; letter-spacing: 0.3px;
  }
  .contact__title { font-size: 15.5px; margin-top: 1px; margin-left: 2px; }
  .contact__address { font-size: 16px; line-height: 20px; margin-top: 25px; margin-left: 2px; }
  .contact__list { list-style: none; margin-top: 19px; margin-left: 2px; font-size: 16px; }
  .contact__list li { display: flex; align-items: center; height: 20px; }
  .contact__list svg { width: 13px; height: 13px; margin-right: 11px; fill: var(--green); }
  .brand {
    display: flex; align-items: center; gap: 10px;
    color: var(--ink); font-weight: 900; letter-spacing: 0.5px;
  }
  .brand__mark { background: var(--green); }
  .card--front .brand { position: absolute; left: 372px; top: 186px; font-size: 32px; }
  .card--front .brand__mark { width: 22px; height: 22px; }
  .card--back .brand { font-size: 58px; gap: 16px; margin-top: 10px; }
  .card--back .brand__mark { width: 40px; height: 40px; background: var(--ink); }
</style>
</head>
<body>
<main class="canvas">
  <section class="card card--front" aria-label="Card front">
    <svg class="front-shape" viewBox="0 0 640 364" aria-hidden="true">
      <path d="M452 0 L282 164 Q262 182 282 200 L438 364 L640 364 L640 0 Z" fill="var(--green)"/>
      <path d="M446 0 L276 164 Q256 182 276 200 L432 364" fill="none" stroke="var(--white)" stroke-width="3"/>
      <path d="M458 0 L292 164 Q274 182 292 200 L446 364 L640 364 L640 0 Z" fill="var(--paper)"/>
    </svg>
    <div class="contact">
      <h1 class="contact__name">MARCUS HALE</h1>
      <p class="contact__title">President</p>
      <p class="contact__address">2710 Cedarbrook Lane<br>Riverton, NJ 08077</p>
      <ul class="contact__list">
        <li><svg viewBox="0 0 24 24"><path d="M6.6 10.8a15.2 15.2 0 0 0 6.6 6.6l2.2-2.2c.3-.3.7-.4 1-.2 1.1.4 2.3.6 3.6.6.6 0 1 .4 1 1V20c0 .6-.4 1-1 1C10.6 21 3 13.4 3 4c0-.6.4-1 1-1h3.5c.6 0 1 .4 1 1 0 1.3.2 2.5.6 3.6.1.3 0 .7-.2 1z"/></svg>(555) 0148-3390</li>
        <li><svg viewBox="0 0 24 24"><path d="M2 5h20v14H2z M2 5l10 8 10-8" /></svg>info@ridgecrest.com</li>
        <li><svg viewBox="0 0 24 24"><circle cx="12" cy="12" r="10"/></svg>www.ridgecrest.com</li>
      </ul>
    </div>
    <div class="brand"><span class="brand__mark"></span>RIDGECREST</div>
  </section>

  <section class="card card--back" aria-label="Card back">
    <div class="brand"><span class="brand__mark"></span>RIDGECREST</div>
  </section>
</main>
</body>
</html>
```